Design website home page for pathology consulting company

Starting a new consulting company with anatomic pathologists focused on expert diagnosis and second opinions on difficult pathology cases. In the near future we will be incorporating next generation diagnostics for rare diseases of childhood into the business. These include discovery and testing of DNA for mutations.

The company is formed around one of the best known pathologists in the world named Marcel "Biscuit" Trowell. The name of the company is "BiscuitLab"

We had a logo design by SketchForum - it is great. I will attach file as soon as I have it (contest ending today). Our company is medical, uses microscopes, DNA, probably will focus on childhood diseases but not solely on childhood diseases. we're not particularly conservative, but the customers we want to appeal to include older practicing pathologists as well as patients (sometimes parents) looking for second opinions.

Think a group of expert doctors diagnosing disease through the microscope and through DNA technology, ages ranging from 35-75 all trained by the best pathologist in the world - "Biscuit"

We receive glass slides from diseases from patients all over the world from docs who need an expert to tell them what is the diagnosis. So "path to the diagnosis" is also part of the company marketing message.

We want the website design to describe our company but be very simple to find what one is looking for as we will use it as the launch page to:
1) order services
2) check results/reports
3) set up new account
4) speak with one of the pathologists
5) see our test menu
6) access our educational material/webinars
Updates

Update - looking for home page design and then finalists will ask for second page design to keep with theme - ok?

Reason: realized this project isn't web design but web home page design - thanks

Reason: Holidays for some in next two weeks

Reason: Hot discussion among collaborators for a few of the submissions. Will provide detail individually this weekend. Thanks so much for all the submissions!

Target Market(s)

Referring pathologists, physicians who want second opinions on pathology disease diagnosis, patients who have had biopsies (either patients themselves or parents of patients), generally high education level

Industry/Entity Type

Marketing

Requirements
Must have
• BiscuitLab
Next Generation Pathology Consultants

```html
<!DOCTYPE html>
<html lang="en">
<head>
<meta charset="utf-8">
<title>BiscuitLab – Next Generation Pathology Consultants</title>
<link rel="stylesheet" href="https://fonts.googleapis.com/css2?family=Open+Sans:wght@300;400;600;700&display=swap">
<style>
:root{
  --black:#000;
  --nav-active:#0b6cb3;
  --brand:#0b6cb3;
  --brand-dark:#0d4d8a;
  --link:#1a7cc0;
  --text:#555;
  --heading:#222;
  --band:#e6e6e6;
  --rule:#d8d8d8;
  --white:#fff;
}
*{margin:0;padding:0;box-sizing:border-box}
html,body{width:983px;height:1200px;overflow:hidden;background:var(--white)}
body{font-family:"Open Sans",sans-serif;color:var(--text)}
.page{position:relative;width:983px;height:1200px;overflow:hidden}

/* top navigation */
.topnav{position:absolute;left:0;top:0;width:983px;height:37px;background:var(--black)}
.topnav a{position:absolute;top:0;height:37px;line-height:37px;color:var(--white);font-size:10.6px;font-weight:600;text-decoration:none;transform:translateX(-50%);white-space:nowrap}
.topnav a.active{background:var(--nav-active);width:63px;text-align:center;left:111px}

/* header */
.social{position:absolute;top:61px;left:80px;display:flex;gap:3px}
.social span{width:23px;height:23px;border:1.5px solid #ddd;border-radius:50%}
.brand{position:absolute;left:391px;top:5px;width:200px;text-align:center}
.brand-mark{display:block;width:68px;height:68px;margin:0 auto;border-radius:50%;background:var(--white);border:3px solid #cfd6dd}
.brand-name{display:block;margin-top:-2px;font-size:20px;font-weight:600;color:var(--brand);letter-spacing:.5px;line-height:22px}
.brand-tag{display:block;font-size:6.5px;color:#888;line-height:9px}
.header-btn{position:absolute;top:59px;height:26px;line-height:26px;text-align:center;color:var(--white);font-size:10.5px;text-decoration:none}
.btn-account{left:613px;width:117px;background:#000}
.btn-speak{left:739px;width:163px;background:linear-gradient(#1ea3de,#0a72b5)}

/* hero */
.hero{position:absolute;left:0;top:109px;width:983px;height:389px;background:linear-gradient(90deg,#8fb0c4 0%,#c8dde8 30%,#9fd2ef 55%,#bfe3f5 75%,#9fcbe2 100%)}
.hero-copy{position:absolute;left:633px;top:127px;width:275px}
.hero-title{font-size:23px;font-weight:600;color:var(--brand);line-height:28px}
.hero-sub{font-size:13.5px;font-weight:700;color:var(--brand);margin-top:2px;line-height:18px;white-space:nowrap}
.hero-text{font-size:9.8px;line-height:17px;color:var(--text);margin-top:8px}
.hero-btn{display:inline-block;margin-top:14px;width:107px;height:29px;line-height:27px;text-align:center;background:#1c1c1c;border:1px solid #555;color:var(--white);font-size:10.5px;font-weight:600;text-decoration:none}

/* feature band */
.features{position:absolute;left:0;top:498px;width:983px;height:262px;background:var(--band)}
.feature{position:absolute;top:32px;width:300px;transform:translateX(-50%);text-align:center}
.feature svg{display:block;margin:0 auto}
.feature h2{margin-top:14px;font-size:19px;line-height:26px;font-weight:400;color:var(--heading);letter-spacing:.2px;white-space:nowrap}
.feature a{display:inline-block;margin-top:10px;width:87px;height:23px;line-height:23px;background:var(--brand-dark);color:var(--white);font-size:12px;text-decoration:none}

/* content */
.content{position:absolute;left:0;top:760px;width:983px;height:399px}
.col-title{position:absolute;top:34px;font-size:19.5px;font-weight:400;color:var(--heading);white-space:nowrap}
.services{position:absolute;left:80px;width:245px}
.services p{position:absolute;top:92px;font-size:11.2px;line-height:17px;font-weight:300;color:#444;width:245px}
.service-list{position:absolute;top:153px;list-style:none;width:245px}
.service-list li{display:flex;align-items:center;height:24.6px;font-size:8.3px;text-transform:uppercase;color:#444;white-space:nowrap}
.service-list li::before{content:"";flex:none;width:10px;height:10px;margin-right:14px;background:var(--brand)}
.service-list li:first-child{text-decoration:underline}
.feature-story{position:absolute;left:359px;width:314px}
.story-photo{position:absolute;top:39px;width:314px;height:115px;background:linear-gradient(90deg,#d9b49e 0%,#e4e8ec 40%,#4c7bb0 75%,#2e5c96 100%)}
.story-title{position:absolute;top:168px;width:314px;font-size:17px;line-height:23px;font-weight:400;color:var(--link);text-transform:uppercase;letter-spacing:-.2px}
.story-text{position:absolute;font-size:10.8px;line-height:17px;font-weight:300;color:#444;width:314px}
.news{position:absolute;left:704px;width:198px}
.news-item{position:absolute;left:0;width:198px;border-bottom:1px solid var(--rule);height:81px}
.news-item h3{font-size:13.8px;font-weight:400;color:var(--link);line-height:18px}
.news-item p{margin-top:9px;font-size:11.2px;line-height:17px;font-weight:300;color:#444}
.read-more{position:absolute;top:341px;width:80px;height:30px;line-height:30px;text-align:center;background:#eee;font-size:9px;color:#333;text-decoration:none}

/* footer */
.footer{position:absolute;left:0;top:1159px;width:983px;height:41px;background:var(--black);color:var(--white)}
.footer small{position:absolute;left:82px;top:0;line-height:41px;font-size:9.5px;font-weight:300}
.footer-social{position:absolute;right:80px;top:13px;display:flex;gap:8px}
.footer-social span{width:14px;height:14px;border-radius:50%;background:var(--white)}
</style>
</head>
<body>
<div class="page">

  <nav class="topnav">
    <a class="active" href="#">Home</a>
    <a href="#" style="left:197px">About Us</a>
    <a href="#" style="left:287px">Services</a>
    <a href="#" style="left:396px">Pathology Consultants</a>
    <a href="#" style="left:553px">Patients</a>
    <a href="#" style="left:655px">Results</a>
    <a href="#" style="left:763px">Accounts</a>
    <a href="#" style="left:875px">Contact Us</a>
  </nav>

  <header>
    <div class="social" aria-label="Social links"><span></span><span></span><span></span><span></span></div>
    <div class="brand">
      <span class="brand-mark"></span>
      <span class="brand-name">BiscuitLab</span>
      <span class="brand-tag">Next Generation Pathology Consultants</span>
    </div>
    <a class="header-btn btn-account" href="#">Setup New Account</a>
    <a class="header-btn btn-speak" href="#">Speak With Pathologist</a>
  </header>

  <section class="hero" role="img" aria-label="Lab scientist in safety glasses at a microscope holding a molecule model, bright blue laboratory background">
    <div class="hero-copy">
      <h1 class="hero-title">BiscuitLab</h1>
      <p class="hero-sub">Next Generation Pathology Consultants</p>
      <p class="hero-text">Sed ut perspiciatis unde omnis iste natus error sit voluptatem accusantium doloremque laudantium, totam rem aperiam, eaque ipsa quae ab illo inventore veritatis et quasi architecto beatae vitae dicta sunt explicabo.</p>
      <a class="hero-btn" href="#">Discover More</a>
    </div>
  </section>

  <section class="features">
    <div class="feature" style="left:196px">
      <svg width="132" height="132" viewBox="0 0 132 132" aria-hidden="true">
        <circle cx="66" cy="66" r="62" fill="none" stroke="#0b6cb3" stroke-width="7"/>
        <g fill="none" stroke="#0b6cb3" stroke-width="3">
          <ellipse cx="66" cy="66" rx="31" ry="12"/>
          <ellipse cx="66" cy="66" rx="31" ry="12" transform="rotate(60 66 66)"/>
          <ellipse cx="66" cy="66" rx="31" ry="12" transform="rotate(-60 66 66)"/>
        </g>
        <circle cx="66" cy="66" r="6" fill="#0b6cb3"/>
      </svg>
      <h2>OUR TEST MENU</h2>
      <a href="#">Click Here</a>
    </div>
    <div class="feature" style="left:491px">
      <svg width="132" height="132" viewBox="0 0 132 132" aria-hidden="true">
        <circle cx="66" cy="66" r="62" fill="none" stroke="#0b6cb3" stroke-width="7"/>
        <g fill="#0b6cb3">
          <rect x="60" y="34" width="10" height="34" rx="2" transform="rotate(35 65 51)"/>
          <rect x="44" y="86" width="46" height="6" rx="2"/>
          <rect x="56" y="64" width="16" height="5"/>
          <path d="M76 62a20 20 0 0 1 -4 24h-8a16 16 0 0 0 4 -22z"/>
          <rect x="60" y="72" width="8" height="14"/>
        </g>
      </svg>
      <h2>PATHOLOGY CONSULTANTS</h2>
      <a href="#">Click Here</a>
    </div>
    <div class="feature" style="left:787px">
      <svg width="132" height="132" viewBox="0 0 132 132" aria-hidden="true">
        <circle cx="66" cy="66" r="62" fill="none" stroke="#0b6cb3" stroke-width="7"/>
        <g fill="#0b6cb3">
          <circle cx="50" cy="70" r="17"/><circle cx="68" cy="56" r="20"/><circle cx="84" cy="70" r="15"/>
          <rect x="42" y="70" width="48" height="17" rx="8"/>
        </g>
        <rect x="56" y="52" width="20" height="28" rx="3" fill="#fff"/>
        <rect x="59" y="47" width="14" height="5" fill="#fff"/>
        <path d="M63 66h6M66 63v6" stroke="#0b6cb3" stroke-width="3"/>
      </svg>
      <h2>CARE ADVICE</h2>
      <a href="#">Click Here</a>
    </div>
  </section>

  <main class="content">
    <section class="services">
      <h2 class="col-title">OUR SERVICES</h2>
      <p>Sed ut perspiciatis unde omnis iste natus error sit voluptatem accusantium doloremque laudantium, totam rem aperiam.</p>
      <ul class="service-list">
        <li>Autopsy Pathology</li>
        <li>Bone and Soft Tissue Pathology</li>
        <li>Clinically Interactive Consultative</li>
        <li>Dermatopathology</li>
        <li>Forensic Pathology</li>
        <li>Gastrointestinal &amp; Hepatic</li>
        <li>Hematology &amp; Hemato</li>
        <li>Immunopathology/Histopathology</li>
        <li>Pediatric Pathology</li>
      </ul>
    </section>

    <section class="feature-story">
      <div class="story-photo" role="img" aria-label="Smiling lab technician in a white coat at a busy laboratory bench"></div>
      <h2 class="story-title">Sed ut perspiciatis unde omnis iste natus error sit voltatem accntim doloremque</h2>
      <p class="story-text" style="top:248px">Sed ut perspiciatis unde omnis iste natus error sit voluptatem accusantium doloremque laudantium, totam rem aperiam, eaque ipsa quae ab illo inventore veritatis et quasi architecto beatae vitae dicta sunt explicabo.</p>
      <p class="story-text" style="top:333px">Nemo enim ipsam voluptatem quia voluptas sit aspernatur aut odit aut fugit, sed quia consequuntur.</p>
    </section>

    <section class="news">
      <h2 class="col-title">NEW SERVICES</h2>
      <div class="news-item" style="top:77px">
        <h3>1. Cosmetic Surgery</h3>
        <p>Sed ut perspiciatis unde omnis iste natus error sit voluptatem</p>
      </div>
      <div class="news-item" style="top:158px">
        <h3>2. Minor Oral Surgery</h3>
        <p>Sed ut perspiciatis unde omnis iste natus error sit voluptatem</p>
      </div>
      <div class="news-item" style="top:239px">
        <h3>3. Restorative Services</h3>
        <p>Sed ut perspiciatis unde omnis iste natus error sit voluptatem</p>
      </div>
      <a class="read-more" href="#">READ MORE</a>
    </section>
  </main>

  <footer class="footer">
    <small>Copyright © 2013 Slidewise Consultants, Inc . All Rights Reserved</small>
    <div class="footer-social" aria-label="Social links"><span></span><span></span><span></span><span></span></div>
  </footer>

</div>
</body>
</html>
```